Pine Hollow Haven Home Inc. Website Update

We have a couple of broken links such as the "contact us" and would like to add board members and a calendar of events. We are open to a new design.

```html
<!DOCTYPE html>
<html lang="en">
<head>
<meta charset="utf-8">
<title>Pine Hollow Haven Home</title>
<link href="https://fonts.googleapis.com/css2?family=Prata&family=Roboto:wght@400;500;700&display=swap" rel="stylesheet">
<style>
:root{
  --blue:#1d5fa7;
  --blue-dark:#174d8c;
  --navy:#1b2f52;
  --pink:#d94a70;
  --pink-soft:#d9607f;
  --ink:#2b2b2b;
  --grey:#6d6d6d;
  --light:#f3f4f6;
  --white:#ffffff;
}
*{margin:0;padding:0;box-sizing:border-box}
html,body{width:1200px;height:5172px;overflow:hidden}
body{position:relative;background:var(--white);font-family:"Roboto",Arial,sans-serif;color:var(--ink)}
.abs{position:absolute}
.serif{font-family:"Prata",Georgia,serif;font-weight:400}
.section{position:absolute;left:0;width:1200px}
.btn{position:absolute;display:flex;align-items:center;justify-content:center;gap:8px;border-radius:24px;font-weight:700;font-size:14px;letter-spacing:.3px;text-transform:uppercase}
.btn-blue{background:var(--blue);color:var(--white)}
.photo{position:absolute}

/* top bar */
.topbar{top:0;height:42px;background:var(--blue);color:var(--white);font-size:14px}
.topbar .item{position:absolute;top:12px;display:flex;align-items:center;gap:8px}
.topbar .donate{position:absolute;left:915px;top:0;width:170px;height:42px;background:var(--pink);display:flex;align-items:center;justify-content:center;font-weight:700;font-size:15px}

/* header */
.header{top:42px;height:148px;background:var(--white)}
.nav{position:absolute;top:66px;left:0;width:1200px;font-weight:700;font-size:15px;color:var(--ink)}
.nav span{position:absolute}
.brand{position:absolute;left:112px;top:10px;width:210px;height:210px;border-radius:50%;background:var(--white);border:6px solid var(--pink);z-index:3;display:flex;align-items:center;justify-content:center;text-align:center;font-family:"Prata",Georgia,serif;font-size:21px;line-height:1.25;color:var(--pink);padding:20px}

/* hero */
.hero{top:190px;height:660px}
.hero .photo{left:0;top:0;width:1200px;height:660px;background:linear-gradient(100deg,#3b2e2a 0%,#6a5246 35%,#b98f75 60%,#8b3a3f 80%,#5a4036 100%)}
.hero h1{position:absolute;left:110px;top:245px;font-size:52px;color:var(--white)}
.hero .tagline{position:absolute;left:100px;top:322px;width:525px;padding:14px 12px;background:rgba(20,30,50,.45);font-size:37px;line-height:1.3;color:var(--white)}

/* services */
.services{top:850px;height:850px;background:linear-gradient(#ffffff,#f4f6f9 50%,#ffffff)}
.title{position:absolute;left:0;width:1200px;text-align:center;font-size:42px;color:var(--blue)}
.sub{position:absolute;left:0;width:1200px;text-align:center;font-size:14px;line-height:25px;color:var(--grey)}
.service{position:absolute;width:210px;height:210px;border-radius:50%;background:var(--white);box-shadow:0 4px 22px rgba(0,0,0,.12);display:flex;flex-direction:column;align-items:center;justify-content:center;gap:14px;font-weight:700;font-size:15px;text-transform:uppercase;color:var(--ink)}
.service.active{background:var(--pink-soft);color:var(--white)}
.service svg{width:66px;height:60px}

/* success */
.success{top:1740px;height:560px}
.success h2{position:absolute;left:0;width:1200px;top:95px;text-align:center;font-size:42px;line-height:52px;color:var(--white)}
.success p{position:absolute;left:300px;width:600px;top:215px;text-align:center;font-size:14px;line-height:23px;color:var(--white)}
.success .donate-btn{position:absolute;left:492px;top:320px;width:216px;height:48px;background:var(--white);color:var(--pink);border-radius:24px;display:flex;align-items:center;justify-content:center;gap:10px;font-weight:700;font-size:16px}

/* stories */
.stories{top:2300px;height:640px}
.stories h2{position:absolute;left:110px;top:65px;font-size:42px;color:var(--ink)}
.stories p{position:absolute;left:110px;width:480px;font-size:14px;line-height:24px;color:var(--grey)}
.divider{position:absolute;left:110px;top:580px;width:980px;height:1px;background:#d8d8d8}

/* board */
.board{top:2940px;height:560px;background:linear-gradient(#fff,#f6f7f9)}
.member{position:absolute;width:240px;text-align:center}
.member .photo{position:relative;margin:0 auto;width:170px;height:170px;border-radius:50%;border:5px solid var(--white);box-shadow:0 3px 14px rgba(0,0,0,.15)}
.member .name{margin-top:22px;font-weight:700;font-size:21px;color:var(--ink)}
.member .role{margin-top:10px;font-size:14px;line-height:25px;color:var(--grey)}

/* testimonials */
.clients{top:3500px;height:560px}
.clients .title{color:var(--white)}
.quote{position:absolute;width:470px;height:150px}
.quote .photo{left:0;top:0;width:120px;height:120px;border-radius:50%;border:5px solid var(--white)}
.quote .mark{position:absolute;left:44px;top:112px;width:32px;height:32px;border-radius:50%;background:var(--blue)}
.quote p{position:absolute;left:150px;top:0;width:320px;font-size:12.5px;line-height:20px;color:var(--white)}
.quote .who{position:absolute;left:150px;top:102px;font-size:12.5px;color:var(--white)}
.quote .who b{font-weight:700}
.arrow{position:absolute;width:30px;height:30px;border-radius:50%;background:rgba(255,255,255,.85);display:flex;align-items:center;justify-content:center}

/* calendar */
.calendar{top:4060px;height:580px}
.calendar .panel{position:absolute;left:60px;top:110px;width:590px;height:390px;background:var(--light)}
.calendar h2{position:absolute;left:110px;top:120px;font-size:46px;line-height:56px;color:var(--ink)}
.date{position:absolute;top:245px;width:96px;height:96px;text-align:center;padding-top:14px}
.date b{display:block;font-family:"Prata",Georgia,serif;font-weight:400;font-size:38px;line-height:40px;color:var(--blue)}
.date small{display:block;font-size:12px;color:var(--grey);text-transform:uppercase}
.date.today{border-radius:50%;background:var(--white);box-shadow:0 2px 10px rgba(0,0,0,.15);border-top:3px solid var(--pink)}
.date.today b{color:var(--ink)}

/* footer */
.footer{top:4660px;height:512px}
.footer .brand-foot{position:absolute;left:120px;top:180px;width:210px;height:210px;border-radius:50%;background:var(--white);display:flex;align-items:center;justify-content:center;text-align:center;padding:22px;font-family:"Prata",Georgia,serif;font-size:21px;line-height:1.25;color:var(--pink)}
.footer h4{position:absolute;font-weight:700;font-size:16px;color:var(--white);text-transform:uppercase}
.contact-row{position:absolute;left:470px;display:flex;align-items:flex-start;gap:16px;font-size:13.5px;line-height:20px;color:var(--white)}
.contact-row svg{width:16px;height:18px;flex:none;margin-top:1px}
.footer .news-text{position:absolute;left:820px;top:222px;width:280px;font-size:14px;line-height:21px;color:var(--white)}
.footer .field{position:absolute;left:820px;top:276px;width:265px;height:38px;border:1px solid var(--white);padding:10px 12px;font-size:13px;color:var(--white)}
.footer .subscribe{position:absolute;left:820px;top:330px;width:108px;height:32px;border-radius:16px;background:var(--pink);color:var(--white);font-size:12px;font-weight:700;display:flex;align-items:center;justify-content:center}
.footer .rule{position:absolute;left:110px;top:402px;width:980px;height:1px;background:rgba(255,255,255,.35)}
.social{position:absolute;top:408px;width:40px;height:40px;border-radius:50%;border:2px solid var(--white);background:var(--navy)}
.footer .copy{position:absolute;left:0;width:1200px;top:462px;text-align:center;font-size:13.5px;color:var(--white)}
</style>
</head>
<body>

<!-- top bar -->
<div class="section topbar">
  <div class="item" style="left:112px">
    <svg width="14" height="14" viewBox="0 0 24 24"><path fill="#fff" d="M6.6 10.8a15 15 0 0 0 6.6 6.6l2.2-2.2c.3-.3.7-.4 1-.2 1.1.4 2.3.6 3.6.6.6 0 1 .4 1 1V20c0 .6-.4 1-1 1A17 17 0 0 1 3 4c0-.6.4-1 1-1h3.5c.6 0 1 .4 1 1 0 1.3.2 2.5.6 3.6.1.3 0 .7-.2 1z"/></svg>
    555.014.2287
  </div>
  <div class="item" style="left:270px">
    <svg width="16" height="12" viewBox="0 0 24 18"><rect x="1" y="1" width="22" height="16" rx="2" fill="#fff"/><path d="M2 2l10 8 10-8" stroke="#1d5fa7" stroke-width="2" fill="none"/></svg>
    hello@pinehollowhaven.org
  </div>
  <div class="donate">DONATE NOW</div>
</div>

<!-- header -->
<div class="section header">
  <div class="brand">Pine Hollow Haven Home</div>
  <nav class="nav">
    <span style="left:432px">HOME</span>
    <span style="left:514px">ABOUT</span>
    <span style="left:606px">HOW YOU CAN HELP</span>
    <span style="left:800px">SERVICES</span>
    <span style="left:912px">MORE &#9662;</span>
    <span style="left:1008px">CONTACT</span>
  </nav>
</div>

<!-- hero -->
<section class="section hero">
  <div class="photo" role="img" aria-label="Photo of two smiling young women talking while holding books"></div>
  <h1 class="serif">OUR MISSION</h1>
  <div class="tagline serif">Giving Girls Roots, Giving Girls Wings</div>
  <svg class="abs" style="left:0;top:540px" width="1200" height="120" viewBox="0 0 1200 120">
    <path d="M0 40 Q600 150 1200 40 L1200 120 L0 120Z" fill="#fff"/>
    <path d="M0 40 Q600 150 1200 40" stroke="#1d5fa7" stroke-width="9" fill="none"/>
    <path d="M0 52 Q600 160 1200 52" stroke="#d94a70" stroke-width="3" fill="none"/>
  </svg>
</section>

<!-- services -->
<section class="section services">
  <h2 class="title serif" style="top:45px">OUR SERVICES</h2>
  <div class="sub" style="top:110px">With the help of our community, we have raised over 1000 girls and counting!<br>Some of the services we offer include</div>

  <div class="service" style="left:112px;top:210px">
    <svg viewBox="0 0 66 60"><path d="M8 28 L33 8 L58 28" stroke="#1d5fa7" stroke-width="3" fill="none"/><rect x="15" y="27" width="36" height="28" stroke="#1d5fa7" stroke-width="3" fill="none"/><rect x="28" y="38" width="10" height="17" fill="#d94a70"/></svg>
    Living Housing
  </div>
  <div class="service active" style="left:367px;top:210px">
    <svg viewBox="0 0 66 60"><rect x="12" y="30" width="42" height="24" stroke="#fff" stroke-width="3" fill="none"/><rect x="17" y="20" width="32" height="10" stroke="#fff" stroke-width="3" fill="none"/><path d="M25 18V8M33 18V6M41 18V8" stroke="#fff" stroke-width="3"/></svg>
    Birthday Parties
  </div>
  <div class="service" style="left:623px;top:210px">
    <svg viewBox="0 0 66 60"><rect x="16" y="6" width="34" height="46" stroke="#1d5fa7" stroke-width="3" fill="none"/><path d="M22 18h22M22 26h22M22 34h14" stroke="#d94a70" stroke-width="3"/><path d="M40 48l14-14" stroke="#1d5fa7" stroke-width="3"/></svg>
    Resume Writing
  </div>
  <div class="service" style="left:878px;top:210px">
    <svg viewBox="0 0 66 60"><circle cx="40" cy="14" r="5" fill="#d94a70"/><path d="M6 36q7-6 14 0t14 0 14 0 14 0M6 46q7-6 14 0t14 0 14 0 14 0" stroke="#1d5fa7" stroke-width="3" fill="none"/></svg>
    Swimming
  </div>
  <div class="service" style="left:112px;top:465px">
    <svg viewBox="0 0 66 60"><rect x="14" y="6" width="32" height="44" stroke="#1d5fa7" stroke-width="3" fill="none"/><path d="M20 18h20M20 26h20" stroke="#1d5fa7" stroke-width="3"/><circle cx="46" cy="42" r="11" fill="#d94a70"/><path d="M41 42l4 4 6-7" stroke="#fff" stroke-width="2.5" fill="none"/></svg>
    Job Placement
  </div>
  <div class="service" style="left:367px;top:465px">
    <svg viewBox="0 0 66 60"><path d="M18 46L48 16" stroke="#1d5fa7" stroke-width="4"/><rect x="8" y="38" width="14" height="8" transform="rotate(-45 15 42)" fill="#d94a70"/><rect x="44" y="14" width="14" height="8" transform="rotate(-45 51 18)" fill="#d94a70"/></svg>
    Daily Exercise
  </div>
  <div class="service" style="left:623px;top:465px">
    <svg viewBox="0 0 66 60"><path d="M8 34h50a25 18 0 0 1-50 0z" stroke="#1d5fa7" stroke-width="3" fill="none"/><path d="M20 30V14M28 30V10M36 30V12M44 30V16" stroke="#d94a70" stroke-width="3"/></svg>
    Nutritional Plan
  </div>
  <div class="service" style="left:878px;top:465px">
    <svg viewBox="0 0 66 60"><circle cx="30" cy="32" r="22" stroke="#1d5fa7" stroke-width="3" fill="none"/><circle cx="30" cy="32" r="13" stroke="#d94a70" stroke-width="3" fill="none"/><circle cx="30" cy="32" r="4" fill="#1d5fa7"/><path d="M30 32L56 8" stroke="#1d5fa7" stroke-width="3"/></svg>
    Goal Planning
  </div>

  <div class="btn btn-blue" style="left:475px;top:730px;width:250px;height:46px">View All Services
    <svg width="14" height="14" viewBox="0 0 16 16"><circle cx="8" cy="8" r="8" fill="#fff"/><path d="M6 4l4 4-4 4" stroke="#1d5fa7" stroke-width="2" fill="none"/></svg>
  </div>
</section>

<!-- success stories band -->
<section class="section success">
  <svg class="abs" style="left:0;top:0" width="1200" height="560" viewBox="0 0 1200 560">
    <defs><linearGradient id="bandBlue" x1="0" y1="0" x2="1" y2="1"><stop offset="0" stop-color="#1d5fa7"/><stop offset="1" stop-color="#174d8c"/></linearGradient></defs>
    <path d="M0 40 Q600 -30 1200 40 L1200 520 Q600 420 0 520Z" fill="url(#bandBlue)"/>
    <path d="M0 506 Q600 400 1200 506" stroke="#d94a70" stroke-width="5" fill="none"/>
  </svg>
  <h2 class="serif">OVER 500 SUCCESS STORIES AND<br>GROWING STRONG</h2>
  <p>We appreciate donations from our community! It is because of the hearts of those around us that we're able to do what we do. If you're a former resident of the Haven Home and would like to tell us about your experience, please email us at hello@pinehollowhaven.org or come by and see us!</p>
  <div class="donate-btn">
    <svg width="20" height="18" viewBox="0 0 24 20"><path d="M12 19L3 10a5 5 0 0 1 9-6 5 5 0 0 1 9 6z" fill="#d94a70"/></svg>
    DONATE NOW
  </div>
</section>

<!-- our stories -->
<section class="section stories">
  <h2 class="serif">OUR STORIES</h2>
  <p style="top:153px">Pine Hollow Haven Home is home to 31 girls ranging in ages from 12-21. The home has seven bedrooms and four bathrooms with a large spa tub for relaxing. Our kitchen takes on the aroma of a restaurant in the evenings as the girls practice their independent Living Skills with menu planning and preparation in a supervised setting.</p>
  <p style="top:310px">When the girls are not cooking or relaxing in their rooms, they may be found in the family room where community meetings...</p>
  <div class="btn btn-blue" style="left:110px;top:415px;width:176px;height:44px">Read More
    <svg width="14" height="14" viewBox="0 0 16 16"><circle cx="8" cy="8" r="8" fill="#fff"/><path d="M6 4l4 4-4 4" stroke="#1d5fa7" stroke-width="2" fill="none"/></svg>
  </div>
  <svg class="abs" style="left:660px;top:40px" width="440" height="420" viewBox="0 0 440 420">
    <circle cx="220" cy="215" r="200" fill="#f2c8d3"/>
    <rect x="10" y="250" width="70" height="40" fill="#d94a70" transform="rotate(-25 45 270)"/>
    <rect x="360" y="250" width="70" height="40" fill="#d94a70" transform="rotate(25 395 270)"/>
    <circle cx="220" cy="215" r="180" fill="#d94a70"/>
  </svg>
  <div class="photo" role="img" aria-label="Photo of a smiling young woman holding a blue notebook" style="left:705px;top:80px;width:350px;height:350px;border-radius:50%;background:linear-gradient(135deg,#e9e3df,#c9b4a8 50%,#3d6aa6)"></div>
  <svg class="abs" style="left:850px;top:225px" width="60" height="60" viewBox="0 0 60 60"><circle cx="30" cy="30" r="28" fill="rgba(0,0,0,.25)" stroke="#fff" stroke-width="3"/><path d="M24 18l18 12-18 12z" fill="#fff"/></svg>
  <div class="divider"></div>
</section>

<!-- board members -->
<section class="section board">
  <h2 class="title serif" style="top:45px;color:var(--ink)">BOARD MEMBERS</h2>
  <div class="sub" style="top:108px">Startup Operators With Decades of Growth Experience.</div>

  <div class="member" style="left:93px;top:175px">
    <div class="photo" role="img" aria-label="Portrait photo of board member Mara Ellison" style="background:linear-gradient(160deg,#c7b3a6,#6d3b36)"></div>
    <div class="name">Mara Ellison</div>
    <div class="role">Lorem ipsum dolor consectetur<br>adipiscing eiusmod temp</div>
  </div>
  <div class="member" style="left:353px;top:175px">
    <div class="photo" role="img" aria-label="Portrait photo of board member Dana Whitfield" style="background:linear-gradient(160deg,#d8cfc9,#7a5a50);box-shadow:0 0 0 6px #d94a70"></div>
    <div class="name">Dana Whitfield</div>
    <div class="role">Lorem ipsum dolor consectetur<br>adipiscing eiusmod temp</div>
  </div>
  <div class="member" style="left:608px;top:175px">
    <div class="photo" role="img" aria-label="Portrait photo of board member Priya Colton" style="background:linear-gradient(160deg,#cfd3d6,#5a4438)"></div>
    <div class="name">Priya Colton</div>
    <div class="role">Lorem ipsum dolor consectetur<br>adipiscing eiusmod temp</div>
  </div>
  <div class="member" style="left:863px;top:175px">
    <div class="photo" role="img" aria-label="Portrait photo of board member Lena Hartwell" style="background:linear-gradient(160deg,#d6e4ec,#c89a6a)"></div>
    <div class="name">Lena Hartwell</div>
    <div class="role">Lorem ipsum dolor consectetur<br>adipiscing eiusmod temp</div>
  </div>
</section>

<!-- testimonials -->
<section class="section clients">
  <svg class="abs" style="left:0;top:0" width="1200" height="560" viewBox="0 0 1200 560">
    <path d="M0 70 Q600 -40 1200 70 L1200 500 Q600 600 0 500Z" fill="#d9607f"/>
    <path d="M0 525 Q600 625 1200 525" stroke="#1d5fa7" stroke-width="5" fill="none"/>
  </svg>
  <h2 class="title serif" style="top:95px">WHAT OUR CLIENT SAYS</h2>
  <div class="arrow" style="left:14px;top:275px"><svg width="10" height="12" viewBox="0 0 10 12"><path d="M8 1L2 6l6 5" stroke="#555" stroke-width="2" fill="none"/></svg></div>
  <div class="arrow" style="left:1156px;top:275px"><svg width="10" height="12" viewBox="0 0 10 12"><path d="M2 1l6 5-6 5" stroke="#555" stroke-width="2" fill="none"/></svg></div>

  <div class="quote" style="left:110px;top:225px">
    <div class="photo" role="img" aria-label="Portrait photo of client Carla Benton" style="background:linear-gradient(160deg,#e2d7cf,#6b4a3c)"></div>
    <div class="mark"></div>
    <p>" Magni dolores eos qui ratione voluptatem sequi nesciunt. Neque porro quisquam est, qui dolorem ipsum quia dolor sit amet consectetur adipisci velit sed quia non numquam "</p>
    <div class="who"><b>CARLA BENTON,</b> Creative Manager</div>
  </div>
  <div class="quote" style="left:622px;top:225px">
    <div class="photo" role="img" aria-label="Portrait photo of client Ruth Gaines" style="background:linear-gradient(160deg,#d3cbc4,#5c463b)"></div>
    <div class="mark"></div>
    <p>" Magni dolores eos qui ratione voluptatem sequi nesciunt. Neque porro quisquam est, qui dolorem ipsum quia dolor sit amet consectetur adipisci velit sed quia non numquam "</p>
    <div class="who"><b>RUTH GAINES,</b> Creative Manager</div>
  </div>
</section>

<!-- calendar -->
<section class="section calendar">
  <div class="panel"></div>
  <div class="photo" style="left:535px;top:205px;width:140px;height:175px;background:var(--pink-soft)"></div>
  <div class="photo" role="img" aria-label="Photo of a large two-storey house with trees and a lawn" style="left:565px;top:65px;width:525px;height:295px;background:linear-gradient(180deg,#d9e2ea,#8a9aa4 55%,#5d7a48)"></div>
  <div class="photo" role="img" aria-label="Photo of teenage girls studying together at a table" style="left:680px;top:240px;width:410px;height:280px;background:linear-gradient(135deg,#e9ddd2,#b8876b 55%,#7a4e3d);border:5px solid #fff"></div>
  <h2 class="serif">A CALENDAR OF<br>EVENTS</h2>
  <div class="date" style="left:82px"><b>14</b><small>March</small></div>
  <div class="date today" style="left:182px"><b>15</b><small>March<br>2019</small></div>
  <div class="date" style="left:282px"><b>16</b><small>March</small></div>
  <div class="date" style="left:382px"><b>17</b><small>March</small></div>
  <div class="btn btn-blue" style="left:110px;top:408px;width:224px;height:44px">Book Online Now
    <svg width="14" height="14" viewBox="0 0 16 16"><circle cx="8" cy="8" r="8" fill="#fff"/><path d="M6 4l4 4-4 4" stroke="#1d5fa7" stroke-width="2" fill="none"/></svg>
  </div>
</section>

<!-- footer -->
<footer class="section footer">
  <svg class="abs" style="left:0;top:0" width="1200" height="512" viewBox="0 0 1200 512">
    <path d="M0 55 Q600 -25 1200 55 L1200 512 L0 512Z" fill="#d94a70"/>
    <path d="M0 66 Q600 -10 1200 66 L1200 512 L0 512Z" fill="#1b2f52"/>
  </svg>
  <div class="brand-foot">Pine Hollow Haven Home</div>

  <h4 style="left:470px;top:178px">Contact Us</h4>
  <div class="contact-row" style="top:222px">
    <svg viewBox="0 0 16 20"><path d="M8 0a7 7 0 0 1 7 7c0 5-7 13-7 13S1 12 1 7a7 7 0 0 1 7-7z" fill="#fff"/><circle cx="8" cy="7" r="2.5" fill="#1b2f52"/></svg>
    <span>418 Birchwood Lane, Millbrook,<br>GA 30999, USA</span>
  </div>
  <div class="contact-row" style="top:288px">
    <svg viewBox="0 0 24 24"><path fill="#fff" d="M6.6 10.8a15 15 0 0 0 6.6 6.6l2.2-2.2c.3-.3.7-.4 1-.2 1.1.4 2.3.6 3.6.6.6 0 1 .4 1 1V20c0 .6-.4 1-1 1A17 17 0 0 1 3 4c0-.6.4-1 1-1h3.5c.6 0 1 .4 1 1 0 1.3.2 2.5.6 3.6.1.3 0 .7-.2 1z"/></svg>
    <span>555.014.2287</span>
  </div>
  <div class="contact-row" style="top:334px">
    <svg viewBox="0 0 24 18"><rect x="1" y="1" width="22" height="16" rx="2" fill="#fff"/><path d="M2 2l10 8 10-8" stroke="#1b2f52" stroke-width="2" fill="none"/></svg>
    <span>hello@pinehollowhaven.org</span>
  </div>

  <h4 style="left:820px;top:178px">Newsletter Subscription</h4>
  <div class="news-text">Register your Email Address to get more Information about us</div>
  <div class="field">Email Address</div>
  <div class="subscribe">SUBSCRIBE</div>

  <div class="rule"></div>
  <div class="social" style="left:510px"></div>
  <div class="social" style="left:556px"></div>
  <div class="social" style="left:602px"></div>
  <div class="social" style="left:648px"></div>
  <div class="copy">Copyright © 2019 Pine Hollow Haven Home . All Rights Reserved &nbsp; | &nbsp; Privacy Policy</div>
</footer>

</body>
</html>
```